Half page (a5) ad for a company

I need a design for an ad for a company to be published in a conference catalogue. Please find enclosed the logo for a company. The company is providing health screening services. Ad should be subtle and minimalistic, i.e. logo in the centre and a phrase saying: "Be in charge of your own health" and the website bluefen.co.uk. Also please find enclosed guidlines for colours and fonts to be used.

```html
<!DOCTYPE html>
<html lang="en">
<head>
<meta charset="UTF-8">
<title>Bluefen Private – Half Page Ad</title>
<link href="https://fonts.googleapis.com/css2?family=Montserrat:wght@400;700&display=swap" rel="stylesheet">
<style>
  :root {
    --backdrop: #2d2d2d;
    --paper: #ffffff;
    --brand-red: #e41e26;
    --deep-red: #8a001d;
    --bright-red: #ed1c24;
    --ink: #111111;
    --on-red: #ffffff;
  }
  * { margin: 0; padding: 0; box-sizing: border-box; }
  html, body {
    width: 1200px;
    height: 1200px;
    overflow: hidden;
    background: var(--backdrop);
    font-family: "Montserrat", Arial, sans-serif;
  }
  .ad-page {
    position: absolute;
    left: 216px;
    top: 58px;
    width: 768px;
    height: 1085px;
    background: var(--paper);
    display: flex;
    flex-direction: column;
  }
  .brand-area {
    height: 726px;
    display: flex;
    flex-direction: column;
    align-items: center;
    justify-content: center;
    gap: 44px;
    padding-bottom: 40px;
  }
  .brand-mark {
    width: 130px;
    height: 130px;
    border-radius: 50%;
    background: var(--brand-red);
  }
  .brand-name {
    font-weight: 400;
    font-size: 60px;
    letter-spacing: 0.5px;
    color: var(--brand-red);
    line-height: 1;
  }
  .message-band {
    flex: 1;
    background: linear-gradient(90deg, var(--bright-red) 0%, var(--deep-red) 4%, #b8132a 30%, #dc1a26 55%, var(--bright-red) 80%);
    display: flex;
    flex-direction: column;
    align-items: center;
    padding-top: 100px;
  }
  .tagline {
    color: var(--on-red);
    font-weight: 700;
    font-size: 37px;
    line-height: 1.1;
  }
  .website {
    margin-top: 26px;
    color: var(--ink);
    font-weight: 700;
    font-size: 22px;
    letter-spacing: 0.3px;
  }
</style>
</head>
<body>
  <main class="ad-page">
    <section class="brand-area">
      <div class="brand-mark" aria-hidden="true"></div>
      <h1 class="brand-name">Bluefen Private</h1>
    </section>
    <section class="message-band">
      <p class="tagline">Be in charge of your own health</p>
      <p class="website">bluefen.co.uk</p>
    </section>
  </main>
</body>
</html>
```